Dog treat bakery needs updated bag labels

We're a small-batch dog treat bakery and would like to update our front bag labels to 1) differentiate our line of products and 2) to stand out on shelves. We believe all dogs deserve to eat clean, healthy foods. That's why we bake low-calorie, clean treats made with simple, premium ingredients like teff, amaranth, and sorghum flours and 100% blueberry, carrot, and purple sweet potato. All our treats are made gluten free without preservatives, artificial flavors, soy, corn, wheat, or eggs. Clean treats, happy dogs!

Logo Text

see uploaded files

```html
<!DOCTYPE html>
<html lang="en">
<head>
<meta charset="utf-8">
<title>Perky Pup – Gluten Free Dog Treats Label</title>
<link rel="stylesheet" href="https://fonts.googleapis.com/css2?family=Antonio:wght@200;300;700&family=Oswald:wght@500;600&family=Libre+Baskerville&display=swap">
<style>
  :root {
    --tan: #c4b59a;
    --tan-light: #ddd3c1;
    --charcoal: #333232;
    --white: #ffffff;
    --brand-brown: #776b5c;
    --ring: #c9bda6;
    --fur: #b3a58b;
    --fur-deep: #8f8474;
    --page: #ffffff;
  }
  * { box-sizing: border-box; margin: 0; padding: 0; }
  html, body {
    width: 891px;
    height: 1200px;
    overflow: hidden;
    background: var(--page);
  }
  .label {
    position: absolute;
    left: 46px;
    top: 368px;
    width: 800px;
    height: 463px;
    background: var(--tan);
    overflow: hidden;
  }
  .label__band {
    position: absolute;
    inset: 0;
  }
  .hearts-art {
    position: absolute;
    left: 10px;
    top: 30px;
    width: 220px;
    height: 412px;
    background:
      radial-gradient(ellipse 34% 20% at 62% 22%, rgba(255,255,255,.42), rgba(255,255,255,0) 100%),
      radial-gradient(ellipse 20% 12% at 28% 16%, rgba(255,255,255,.30), rgba(255,255,255,0) 100%),
      radial-gradient(ellipse 16% 10% at 40% 40%, rgba(255,255,255,.30), rgba(255,255,255,0) 100%),
      radial-gradient(ellipse 32% 22% at 34% 66%, rgba(255,255,255,.40), rgba(255,255,255,0) 100%),
      radial-gradient(ellipse 18% 14% at 78% 70%, rgba(255,255,255,.28), rgba(255,255,255,0) 100%),
      radial-gradient(ellipse 18% 12% at 62% 90%, rgba(255,255,255,.30), rgba(255,255,255,0) 100%);
  }
  .center-copy {
    position: absolute;
    left: 191px;
    width: 352px;
    text-align: center;
    color: var(--white);
  }
  .tagline {
    top: 19px;
    font-family: "Libre Baskerville", serif;
    font-size: 16px;
    color: var(--tan);
  }
  .product-type {
    top: 40px;
    font-family: "Oswald", sans-serif;
    font-weight: 500;
    font-size: 44px;
    letter-spacing: 1px;
    line-height: 1;
  }
  .product-name {
    top: 390px;
    font-family: "Libre Baskerville", serif;
    font-size: 22px;
    color: var(--tan);
  }
  .net-weight {
    top: 425px;
    font-family: "Libre Baskerville", serif;
    font-size: 14px;
  }
  .badge {
    position: absolute;
    left: 237px;
    top: 121px;
    width: 256px;
    height: 256px;
    border-radius: 50%;
    background: var(--white);
  }
  .badge__ring {
    position: absolute;
    inset: 12px;
    border-radius: 50%;
    border: 2px solid var(--ring);
    border-top-color: transparent;
    border-bottom-color: transparent;
  }
  .brand-word {
    position: absolute;
    left: 0;
    width: 100%;
    text-align: center;
    font-family: "Oswald", sans-serif;
    font-weight: 600;
    font-size: 30px;
    letter-spacing: 4px;
    color: var(--brand-brown);
    line-height: 1;
  }
  .brand-word--top { top: 16px; }
  .brand-word--bottom { top: 203px; }
  .mascot-art {
    position: absolute;
    left: 48px;
    top: 52px;
    width: 160px;
    height: 150px;
    background:
      radial-gradient(ellipse 38% 34% at 50% 32%, var(--fur) 0%, var(--fur) 70%, rgba(179,165,139,0) 100%),
      radial-gradient(ellipse 34% 44% at 50% 72%, var(--fur-deep) 0%, rgba(143,132,116,.7) 60%, rgba(143,132,116,0) 100%);
  }
  .claims {
    position: absolute;
    left: 601px;
    color: var(--white);
    font-family: "Antonio", sans-serif;
    font-weight: 200;
    font-size: 25px;
    line-height: 32.5px;
  }
  .claims__head {
    font-weight: 700;
    font-size: 23px;
  }
  .claims--free { top: 39px; }
  .claims--made { top: 223px; }
  .calorie-pill {
    position: absolute;
    left: 556px;
    top: 386px;
    width: 203px;
    height: 47px;
    border-radius: 24px;
    background: var(--charcoal);
    color: var(--white);
    font-family: "Antonio", sans-serif;
    font-weight: 200;
    font-size: 27px;
    line-height: 47px;
    text-align: center;
  }
  .calorie-pill strong { font-weight: 700; }
</style>
</head>
<body>
  <main class="label">
    <svg class="label__band" width="800" height="463" viewBox="0 0 800 463" aria-hidden="true">
      <path fill="var(--charcoal)" d="M253 0 L481 0 C492 70 520 130 544 172 L544 294 C520 340 505 400 497 463 L253 463 C245 400 214 340 191 294 L191 172 C214 130 242 70 253 0 Z"/>
      <g fill="var(--white)">
        <circle cx="273" cy="128" r="3.5"/>
        <circle cx="244" cy="134" r="2.5"/>
        <circle cx="258" cy="151" r="2.5"/>
        <circle cx="240" cy="168" r="3.5"/>
        <circle cx="488" cy="137" r="3.5"/>
        <circle cx="471" cy="156" r="2.5"/>
        <circle cx="497" cy="183" r="3.5"/>
        <circle cx="256" cy="335" r="3.5"/>
        <circle cx="490" cy="343" r="4"/>
        <circle cx="262" cy="364" r="3"/>
        <circle cx="453" cy="374" r="3.5"/>
        <circle cx="293" cy="380" r="2.5"/>
      </g>
    </svg>

    <div class="hearts-art" role="img" aria-label="Cluster of hand-drawn white outline hearts"></div>

    <p class="center-copy tagline">gluten free</p>
    <h1 class="center-copy product-type">DOG TREATS</h1>

    <div class="badge">
      <div class="badge__ring"></div>
      <span class="brand-word brand-word--top">PERKY</span>
      <div class="mascot-art" role="img" aria-label="Illustrated mascot dog with its tongue out"></div>
      <span class="brand-word brand-word--bottom">PUP</span>
    </div>

    <p class="center-copy product-name">Maple’s Morsels</p>
    <p class="center-copy net-weight">Net Wt 4 OZ (113g)</p>

    <div class="claims claims--free">
      <p class="claims__head">NO</p>
      <p>SOY, CORN,<br>WHEAT, EGGS<br>OR DAIRY</p>
    </div>

    <div class="claims claims--made">
      <p class="claims__head">MADE WITH</p>
      <p>ANCIENT GRAINS<br>AND GRASS FED<br>BEEF LIVER</p>
    </div>

    <p class="calorie-pill"><strong>10</strong> CALORIES EACH</p>
  </main>
</body>
</html>
```